Business Card Design Project

After recently finishing a design project for the company logo using markbazaar, it's now time for a business card. Attached to this is the logo.

The requirements for the business card are pretty straightforward:

- A clean, uncomplicated look
- Consistent usage of fonts
- Designs for both single sided and double sided cards
- A modern layout with preferably space to refer to social media accounts and/or downloadable vcards through a qr code
- consistent application of the company colour scheme: red/white. Hex codes for exact colour can be provided

Thanks!

```html
<!DOCTYPE html>
<html lang="en">
<head>
<meta charset="utf-8">
<title>Ember Lane Staffing – Business Card</title>
<link rel="stylesheet" href="https://fonts.googleapis.com/css2?family=Open+Sans:wght@400;600;700&display=swap">
<style>
  :root {
    --brand-red: #e01e26;
    --brand-red-deep: #a50d14;
    --ink: #231f20;
    --card: #ffffff;
    --backdrop: #ececec;
    --rule: #b5b5b5;
  }
  * { margin: 0; padding: 0; box-sizing: border-box; }
  html, body {
    width: 960px;
    height: 1200px;
    overflow: hidden;
    background: var(--backdrop);
    font-family: "Open Sans", Arial, sans-serif;
    color: var(--ink);
  }
  .canvas { position: relative; width: 960px; height: 1200px; }
  .card {
    position: absolute;
    width: 840px;
    height: 480px;
    background: var(--card);
    border-radius: 30px;
    overflow: hidden;
    box-shadow: 0 4px 14px rgba(0,0,0,0.12);
  }
  .card--front { left: 67px; top: 96px; }
  .card--back { left: 60px; top: 637px; }

  .swoosh { position: absolute; inset: 0; width: 840px; height: 480px; }

  .wordmark { position: absolute; display: flex; align-items: center; gap: 22px; }
  .wordmark__square { width: 34px; height: 34px; background: var(--brand-red); flex: none; }
  .wordmark__name {
    font-weight: 600;
    color: var(--ink);
    line-height: 1.05;
  }
  .wordmark__name span { display: block; }
  .card--front .wordmark { left: 53px; top: 82px; }
  .card--front .wordmark__name { font-size: 62px; letter-spacing: -1px; }
  .card--back .wordmark { left: 140px; top: 158px; }
  .card--back .wordmark__name { font-size: 72px; letter-spacing: -1px; }

  .contact { position: absolute; left: 57px; top: 306px; }
  .contact__name { font-size: 24px; font-weight: 700; }
  .contact__role { font-size: 20px; font-weight: 400; }
  .contact__list { list-style: none; margin-top: 14px; font-size: 19px; line-height: 30px; }
  .contact__list b { font-style: italic; font-weight: 700; }

  .divider {
    position: absolute;
    left: 368px; top: 336px;
    width: 1px; height: 113px;
    background: var(--rule);
  }
  .address {
    position: absolute;
    left: 396px; top: 388px;
    font-size: 19px;
    line-height: 30px;
    font-style: normal;
  }
</style>
</head>
<body>
<div class="canvas">
  <section class="card card--front">
    <svg class="swoosh" viewBox="0 0 840 480" aria-hidden="true">
      <defs>
        <linearGradient id="swoosh-red" x1="0" y1="0" x2="1" y2="0">
          <stop offset="0" stop-color="var(--brand-red)"/>
          <stop offset="1" stop-color="var(--brand-red-deep)"/>
        </linearGradient>
      </defs>
      <path d="M578,0 C700,60 800,220 705,480 L840,480 L840,0 Z" fill="url(#swoosh-red)"/>
      <path d="M690,0 C770,70 815,230 745,425 C795,250 770,90 722,0 Z" fill="var(--card)"/>
    </svg>

    <div class="wordmark">
      <div class="wordmark__square"></div>
      <div class="wordmark__name"><span>Ember Lane</span><span>Staffing</span></div>
    </div>

    <div class="contact">
      <p><span class="contact__name">Your Name -</span> <span class="contact__role">Designation</span></p>
      <ul class="contact__list">
        <li><b>t</b> : 123-123-1234</li>
        <li><b>e</b> : info@yourwebsite.com</li>
        <li><b>w</b> : www.emberlane.com</li>
      </ul>
    </div>
    <div class="divider"></div>
    <address class="address">1234, Street Name<br>District, City, Country Code.</address>
  </section>

  <section class="card card--back">
    <div class="wordmark">
      <div class="wordmark__square"></div>
      <div class="wordmark__name"><span>Ember Lane</span><span>Staffing</span></div>
    </div>
  </section>
</div>
</body>
</html>
```